Upmarket Dessert Lounge needs a Business Card Design

We are an upmarket dessert lounge needing a business card to match our image.

We want something that is simple yet beautiful, feminine, classy, sophisticated and elegant. We want it to stand out and don't mind if it is bold.

The design should include our logo and colours of red or maroon with gold highlights. We don't mind if black is used.

Marlow & Quince

Target Market(s)

For those who like to indulge or treat themselves and give in to their temptations on good quality desserts.

Industry/Entity Type

Business

Requirements
Must have
• Must include our logo and our name

Marlow & Quince

M & Q

```html
<!DOCTYPE html>
<html lang="en">
<head>
<meta charset="utf-8">
<title>Marlow &amp; Quince — Business Card</title>
<link rel="stylesheet" href="https://fonts.googleapis.com/css2?family=Open+Sans:wght@400;600;700&display=swap">
<style>
  :root {
    --maroon: #7a1416;
    --cream: #fdd19a;
    --paper: #ffffff;
    --ink: #3a3a3a;
    --backdrop: #e6e6e6;
  }
  * { box-sizing: border-box; margin: 0; padding: 0; }
  html, body { width: 956px; height: 1200px; overflow: hidden; }
  body {
    background: var(--backdrop);
    font-family: "Open Sans", Arial, sans-serif;
    position: relative;
  }
  .card {
    position: absolute;
    width: 798px;
    height: 454px;
    background: var(--paper);
    border-radius: 24px;
    overflow: hidden;
  }
  .card--front { left: 79px; top: 104px; }
  .card--back { left: 73px; top: 633px; }
  .card__art { position: absolute; inset: 0; }
  .brand-name {
    position: absolute;
    left: 89px;
    top: 70px;
    width: 302px;
    text-align: center;
    color: var(--maroon);
    font-size: 30px;
    font-weight: 600;
    letter-spacing: 0.5px;
  }
  .contact { position: absolute; left: 89px; top: 226px; color: var(--ink); }
  .contact__name { font-size: 22px; margin-bottom: 14px; }
  .contact__name strong { font-weight: 700; }
  .contact__line { font-size: 18px; line-height: 30px; }
  .contact__line b { font-weight: 700; }
  .footer {
    position: absolute;
    left: 0; right: 0;
    top: 392px;
    text-align: center;
    color: var(--paper);
    font-size: 18px;
    line-height: 27px;
    padding-left: 0;
  }
  .footer b { font-weight: 700; }
  .monogram {
    position: absolute;
    inset: 0;
    display: flex;
    align-items: center;
    justify-content: center;
    color: var(--maroon);
    font-size: 96px;
    font-weight: 600;
    letter-spacing: 2px;
  }
</style>
</head>
<body>
  <section class="card card--front">
    <svg class="card__art" viewBox="0 0 798 454" width="798" height="454" aria-hidden="true">
      <path fill="var(--cream)" d="M683 0 C705 150 630 290 470 372 C640 330 760 250 798 125 L798 0 Z"/>
      <path fill="var(--maroon)" d="M0 395 C140 352 380 392 540 358 C670 330 760 255 798 158 L798 454 L0 454 Z"/>
    </svg>
    <div class="brand-name">Marlow &amp; Quince</div>
    <div class="contact">
      <p class="contact__name"><strong>Your Name -</strong> Designation</p>
      <p class="contact__line"><b>p</b> : 123-456-7890 &nbsp;|&nbsp; <b>c</b> : 123-456-7890</p>
      <p class="contact__line"><b>e</b> : name@yourwebsite.com</p>
    </div>
    <div class="footer">
      <p><b>f</b> : 123-456-7890 &nbsp;| <b>w</b> : www.marlowquince.com</p>
      <p>0000, Street Name, City Name, Country Code.</p>
    </div>
  </section>

  <section class="card card--back">
    <div class="monogram">M &amp; Q</div>
  </section>
</body>
</html>
```